GearHive.com

Our company, GearHive Inc., is an established business with an extensive worldwide customer base in the Aviation, Aerospace, and Defense Industries.
GearHive Inc, is an e-commerce platform driven by an aviation parts locator. We are looking to totally redo our homepage, log-in page, standard part search page, and results page.
Our current web design is in 800frame and we need it to be updated to a centered 1280 frame. The new design also needs to be easily viewed from any mobile device. The new size needs to accommodate 2-3 advertisements, both vertically and horizontally.
I like clean, simple, crisp lines that can easily be navigated by everyone. Along with Aviation/Aerospace stock photos, I would like to use different shades of blue and grey and accent specific buttons/drop-downs with orange or yellow.
We are also looking for a web designer who also has the ability to cut up the page and turn over to our .NET developers.
Attached are the 4 pages that I would like to start working on. The standard content within these pages need to be incorporated into the new design.
Our current website is www.gearhive.com
Below are some industry websites that I like the color and feel of.
Please use attached pic of corvane T410 as main photo
http://www.stravelcorp.com/
http://www.quillanor.com/en/aerospace.html
http://www.dexavend.com/
http://aerospace.veltrimax.com/

```html
<!DOCTYPE html>
<html lang="en">
<head>
<meta charset="utf-8">
<title>GearHive.com – Buy. Sell. Search.</title>
<link href="https://fonts.googleapis.com/css2?family=Raleway:ital,wght@0,400;0,500;0,600;0,700;1,500&family=Nunito:wght@800;900&display=swap" rel="stylesheet">
<style>
:root{
  --blue:#1a9ad6;
  --blue-deep:#2b3990;
  --orange:#f7941d;
  --orange-text:#f26d21;
  --grey-bg:#ececec;
  --text:#555;
  --muted:#8a8a8a;
  --footer:#3b3b3b;
  --white:#fff;
}
*{margin:0;padding:0;box-sizing:border-box}
html,body{width:736px;height:1200px;overflow:hidden}
body{font-family:"Raleway",Arial,sans-serif;color:var(--text);background:var(--white);position:relative}
.abs{position:absolute}

/* header */
.topbar{left:0;top:0;width:736px;height:56px;border-top:2px solid var(--blue-deep);background:var(--white)}
.brand{left:80px;top:20px;font-weight:700;font-size:18px;color:var(--blue-deep);display:flex;align-items:center;gap:6px}
.brand-mark{width:10px;height:10px;background:var(--blue)}
.toplinks{right:144px;top:24px;font-size:7.5px;font-weight:600;color:#555;letter-spacing:.1px}
.toplinks b{color:var(--blue);font-weight:700}
.toplinks span.sep{margin:0 5px;color:#888}
.login{left:609px;top:19px;width:46px;height:23px;background:var(--orange);color:var(--white);font-size:7.5px;font-weight:600;display:flex;align-items:center;justify-content:center}

.mainnav{left:0;top:56px;width:736px;height:35px;background:var(--blue)}
.mainnav ul{list-style:none;position:absolute;left:80px;top:0;height:35px;display:flex}
.mainnav li{color:var(--white);font-size:8px;font-weight:600;height:35px;line-height:35px;padding:0 8.3px}
.mainnav li.active{background:var(--blue-deep)}

/* hero */
.hero{left:0;top:91px;width:736px;height:331px;background:linear-gradient(180deg,#6f9fd0 0%,#9cbfe0 35%,#8d8a6d 70%,#4a4030 100%)}
.hero-plane{left:10px;top:10px;width:700px;height:250px;background:radial-gradient(ellipse at 55% 55%,rgba(245,245,245,.75) 0%,rgba(235,235,235,.45) 45%,rgba(235,235,235,0) 70%)}
.hero-title{left:0;top:171px;width:736px;text-align:center;font-family:"Nunito",Arial,sans-serif;font-weight:900;font-size:33px;color:var(--white);text-shadow:0 1px 3px rgba(0,0,0,.3)}
.hero-sub{left:0;top:216px;width:736px;text-align:center;font-size:20px;font-weight:500;color:var(--white);text-shadow:0 1px 3px rgba(0,0,0,.4)}
.hero-cta{left:236px;top:261px;width:255px;height:38px;background:var(--orange);border:3px solid var(--white);color:var(--white);font-family:"Nunito",Arial,sans-serif;font-weight:800;font-size:16px;display:flex;align-items:center;justify-content:center}
.slide-arrow{top:154px;width:22px;height:22px;border-radius:50%;background:rgba(30,30,30,.75)}
.slide-arrow svg{display:block}

/* features */
.feature{top:455px;width:124px;text-align:center}
.feature .icon{width:36px;height:36px;margin:0 auto;background:var(--blue-deep);display:flex;align-items:center;justify-content:center}
.feature h3{font-size:12px;font-style:italic;font-weight:500;color:var(--blue);margin-top:15px}
.feature hr{border:0;border-top:1px solid #e2e2e2;width:110px;margin:7px auto 8px}
.feature p{font-size:6.4px;line-height:10.5px;color:var(--muted)}
.more{width:38px;height:19px;margin:11px auto 0;background:var(--blue);color:var(--white);font-size:6.5px;font-weight:600;display:flex;align-items:center;justify-content:center}

/* events */
.events{left:0;top:625px;width:736px;height:233px;background:var(--grey-bg)}
.events-head{left:0;top:27px;width:736px;display:flex;justify-content:center;align-items:center;gap:12px;font-size:15px;font-weight:500;color:var(--blue)}
.event{top:66px;width:182px}
.event .pic{height:86px;border:3px solid var(--white)}
.event h4{margin-top:14px;font-size:8px;font-weight:700;color:var(--orange-text)}
.event p{margin-top:9px;font-size:6.3px;line-height:10.5px;color:var(--text)}

/* news */
.section-title{font-size:15px;font-weight:500;color:var(--blue)}
.news-rule{left:80px;top:921px;width:145px;border-top:1px solid #ddd}
.news{top:935px;width:145px}
.news-head{display:flex;gap:9px}
.datebox{width:40px;height:36px;background:var(--blue-deep);color:var(--white);text-align:center;font-weight:700}
.datebox .d{font-size:12px;padding-top:4px;line-height:14px}
.datebox .m{font-size:8px}
.news-meta{font-style:italic;font-size:8px;color:#666;padding-top:2px;font-weight:500}
.news-meta small{display:block;font-size:6.5px;color:#999;margin-top:4px}
.news h4{margin-top:22px;font-size:7.5px;font-weight:700;color:var(--orange-text)}
.news p{margin-top:9px;font-size:7.2px;line-height:11.5px;color:var(--text)}

.testi-box{left:436px;top:920px;width:219px;height:81px;background:var(--blue);color:var(--white);font-size:6.8px;font-style:italic;font-weight:500;line-height:11px;text-align:center;padding:17px 20px}
.testi-pointer{left:462px;top:1000px}
.avatar{left:436px;top:1021px;width:45px;height:39px;background:linear-gradient(135deg,#c99c6e,#7a5a3c)}
.testi-name{left:489px;top:1029px;font-size:9px;font-weight:500;color:var(--blue)}
.testi-role{left:491px;top:1042px;font-size:7px;color:#666}

/* newsletter */
.newsletter{left:0;top:1089px;width:736px;height:52px;background:var(--blue)}
.nl-text{left:80px;top:18px;color:var(--white);font-size:8.6px;font-weight:600}
.nl-text b{font-family:"Nunito",Arial,sans-serif;font-size:14px;font-weight:800;margin-left:2px}
.nl-input{left:407px;top:12px;width:162px;height:28px;background:var(--white);font-size:8px;color:#aaa;padding:9px 7px}
.nl-btn{left:579px;top:12px;width:76px;height:28px;background:var(--blue-deep);color:var(--white);font-size:9px;font-weight:600;display:flex;align-items:center;justify-content:center}

/* footer */
.footer{left:0;top:1141px;width:736px;height:59px;background:var(--footer)}
.social{left:82px;top:18px;display:flex;gap:6px}
.social span{width:22px;height:22px;border:1.5px solid var(--white);border-radius:50%;display:flex;align-items:center;justify-content:center}
.footlinks{right:81px;top:26px;font-size:7px;color:#ddd}
.footlinks i{font-style:normal;margin:0 4px}
</style>
</head>
<body>

<header>
  <div class="abs topbar">
    <div class="abs brand"><span class="brand-mark"></span>GearHive</div>
    <div class="abs toplinks">GEARHIVE <b>MAIN</b><span class="sep">|</span>AERO <b>PAGES</b><span class="sep">|</span>MESSAGE <b>BOARD</b></div>
    <div class="abs login">LOGIN</div>
  </div>
  <nav class="abs mainnav">
    <ul>
      <li class="active">HOME</li><li>ABOUT US</li><li>MEMBERSHIP</li><li>BUYERS</li><li>SUPPLIERS</li><li>GOVERNMENT DATA</li><li>ADVERTISE</li><li>MEDIA</li><li>FAQS</li><li>CONTACT US</li>
    </ul>
  </nav>
</header>

<section class="abs hero" role="img" aria-label="Photo of a white passenger jet parked on grass under a blue sky">
  <div class="abs hero-plane"></div>
  <div class="abs slide-arrow" style="left:13px"><svg width="22" height="22"><path d="M13 7 L9 11 L13 15" stroke="#fff" stroke-width="1.6" fill="none"/></svg></div>
  <div class="abs slide-arrow" style="left:703px"><svg width="22" height="22"><path d="M9 7 L13 11 L9 15" stroke="#fff" stroke-width="1.6" fill="none"/></svg></div>
  <h1 class="abs hero-title">Government Bidding?</h1>
  <p class="abs hero-sub">DETAILED LOGISTICS &amp; NOTIFICATION</p>
  <div class="abs hero-cta">FREE TRIAL! SIGN UP NOW</div>
</section>

<section class="features">
  <div class="abs feature" style="left:80px">
    <div class="icon"><svg width="22" height="22" viewBox="0 0 22 22"><path d="M3 6h5a2.5 2.5 0 1 1 5 0h5v5a2.5 2.5 0 1 0 0 5v3H3v-4a2.5 2.5 0 1 0 0-5z" fill="#fff"/></svg></div>
    <h3>Solutions</h3><hr>
    <p>Lorem ips,consectetur um dolor sit amet,consectetur ipisicing elit, sed do eiusmod tempor incididunt ut labore et</p>
    <div class="more">MORE</div>
  </div>
  <div class="abs feature" style="left:234px">
    <div class="icon"><svg width="22" height="22" viewBox="0 0 22 22"><path d="M17 3l2 2-5 5 2 8-2 1-4-6-4 4v3l-1.5 1-1-3.5L0 16l1-1.5h3l4-4-6-4 1-2 8 2z" fill="#fff"/></svg></div>
    <h3>Our Community</h3><hr>
    <p>Lorem ips,consectetur um dolor sit amet,consectetur ipisicing elit, sed do eiusmod tempor incididunt ut labore et</p>
    <div class="more">MORE</div>
  </div>
  <div class="abs feature" style="left:379px">
    <div class="icon"><svg width="22" height="22" viewBox="0 0 22 22"><path d="M3 20V10l5 3v-3l5 3v-3l6 3v7zM4 2h2v7H4zM8 4h2v6H8z" fill="#fff"/><rect x="6" y="15" width="2" height="2" fill="#2b3990"/><rect x="11" y="15" width="2" height="2" fill="#2b3990"/><rect x="15" y="15" width="2" height="2" fill="#2b3990"/></svg></div>
    <h3>Industry Connections</h3><hr>
    <p>Lorem ips,consectetur um dolor sit amet,consectetur ipisicing elit, sed do eiusmod tempor incididunt ut labore et</p>
    <div class="more">MORE</div>
  </div>
  <div class="abs feature" style="left:533px">
    <div class="icon"><svg width="24" height="22" viewBox="0 0 24 22"><circle cx="12" cy="7" r="3.5" fill="#fff"/><circle cx="5" cy="8" r="2.5" fill="#fff"/><circle cx="19" cy="8" r="2.5" fill="#fff"/><path d="M6 19a6 6 0 0 1 12 0z M0 17a5 4 0 0 1 7-3.5 7 7 0 0 0-2 3.5z M24 17a5 4 0 0 0-7-3.5 7 7 0 0 1 2 3.5z" fill="#fff"/></svg></div>
    <h3>Member Advantages</h3><hr>
    <p>Lorem ips,consectetur um dolor sit amet,consectetur ipisicing elit, sed do eiusmod tempor incididunt ut labore et</p>
    <div class="more">MORE</div>
  </div>
</section>

<section class="abs events">
  <div class="abs events-head">
    <svg width="8" height="12"><path d="M6 1 L2 6 L6 11" stroke="#aaa" stroke-width="2" fill="none"/></svg>
    <span>Our Events</span>
    <svg width="8" height="12"><path d="M2 1 L6 6 L2 11" stroke="#2b3990" stroke-width="2" fill="none"/></svg>
  </div>
  <div class="abs event" style="left:80px">
    <div class="pic" role="img" aria-label="Photo of a large airliner on a runway" style="background:linear-gradient(180deg,#8fb4d6 0%,#c9d7e2 45%,#6f7d5a 75%,#55604a 100%)"></div>
    <h4>LOREM IPSUM DOLOR SIT AMET</h4>
    <p>Consecteturadipisicing elit, sed do eimod cteturadipisicing elit, sed do eiusmod tempor incididunt ut labore et.....</p>
  </div>
  <div class="abs event" style="left:276px">
    <div class="pic" role="img" aria-label="Photo of a jet flying above the clouds" style="background:linear-gradient(180deg,#0f4f9c 0%,#3b86cf 50%,#dfe8f2 80%,#a9bfd8 100%)"></div>
    <h4>LOREM IPSUM DOLOR SIT AMET</h4>
    <p>Consecteturadipisicing elit, sed do eimod cteturadipisicing elit, sed do eiusmod tempor incididunt ut labore et.....</p>
  </div>
  <div class="abs event" style="left:473px">
    <div class="pic" role="img" aria-label="Photo of an airliner in flight against a grey sky" style="background:linear-gradient(180deg,#9ea7b2 0%,#c7ccd2 55%,#b1b8c0 100%)"></div>
    <h4>LOREM IPSUM DOLOR SIT AMET</h4>
    <p>Consecteturadipisicing elit, sed do eimod cteturadipisicing elit, sed do eiusmod tempor incididunt ut labore et.....</p>
  </div>
</section>

<section class="news-block">
  <h2 class="abs section-title" style="left:80px;top:888px">Latest News</h2>
  <div class="abs news-rule"></div>
  <article class="abs news" style="left:80px">
    <div class="news-head">
      <div class="datebox"><div class="d">14</div><div class="m">JULY</div></div>
      <div class="news-meta">Aenean auctor wisi et<small>Posted by Admin</small></div>
    </div>
    <h4>LOREM IPSUM DOLOR SIT AMET.</h4>
    <p>Lorem ips,consectetur um dolor sit amet,consectetur ipisicing elit, sed do eiusmod tempor incididunt ut labore et dolore magna aliqua.</p>
  </article>
  <article class="abs news" style="left:255px">
    <div class="news-head">
      <div class="datebox"><div class="d">14</div><div class="m">JULY</div></div>
      <div class="news-meta">Aenean auctor wisi et<small>Posted by Admin</small></div>
    </div>
    <h4>LOREM IPSUM DOLOR SIT AMET.</h4>
    <p>Lorem ips,consectetur um dolor sit amet,consectetur ipisicing elit, sed do eiusmod tempor incididunt ut labore et dolore magna aliqua.</p>
  </article>
</section>

<section class="testimonials">
  <h2 class="abs section-title" style="left:436px;top:888px">Testimonials</h2>
  <svg class="abs" style="left:636px;top:891px" width="20" height="12"><path d="M6 1 L2 6 L6 11" stroke="#aaa" stroke-width="2" fill="none"/><path d="M14 1 L18 6 L14 11" stroke="#2b3990" stroke-width="2" fill="none"/></svg>
  <blockquote class="abs testi-box">“Lorem ipsum dolor sit amet, consectetur ipisicing elit, sed do eiusmod tempor incididunt ut labore et dolore magna aliqua.Lorem ipsum dolor sit amet, consectetur ipisicing elit, re ...”</blockquote>
  <svg class="abs testi-pointer" width="16" height="9"><path d="M0 0 H16 L8 9z" fill="#1a9ad6"/></svg>
  <div class="abs avatar" role="img" aria-label="Portrait photo of the reviewer"></div>
  <div class="abs testi-name">Dana Mirel Cole</div>
  <div class="abs testi-role">Lorem ipsum dolor</div>
</section>

<section class="abs newsletter">
  <p class="abs nl-text">IF YOU HAVE FRESH IDEAS, SIGN UP FOR OUR<b>NEWSLETTER</b></p>
  <div class="abs nl-input">Name:</div>
  <div class="abs nl-btn">SUBSCRIBE</div>
</section>

<footer class="abs footer">
  <div class="abs social">
    <span><svg width="8" height="10"><rect x="3" y="1" width="2" height="9" fill="#fff"/><rect x="1" y="4" width="6" height="1.6" fill="#fff"/></svg></span>
    <span><svg width="10" height="10"><circle cx="5" cy="5" r="3" fill="#fff"/></svg></span>
    <span><svg width="10" height="10"><circle cx="2" cy="8" r="1.3" fill="#fff"/><path d="M1 4.5a4.5 4.5 0 0 1 4.5 4.5M1 1.5a7.5 7.5 0 0 1 7.5 7.5" stroke="#fff" stroke-width="1.4" fill="none"/></svg></span>
    <span><svg width="10" height="10"><rect x="4" y="1" width="2" height="8" fill="#fff"/><rect x="1" y="4" width="8" height="2" fill="#fff"/></svg></span>
  </div>
  <p class="abs footlinks">Employment<i>|</i>Terms<i>|</i>Contact<i>|</i>Copyright @2014 GearHive. All rights reserved.</p>
</footer>

</body>
</html>
```